Layout for site fence advertising - length approx. 250 cm x 125 cm

The advertising will later be printed on a PVC film and used for events or on sports fields.

Main services :
Your regional contact at
Real estate and business financing
independent insurance advice

```html
<!DOCTYPE html>
<html lang="en">
<head>
<meta charset="utf-8">
<title>Fence Banner – Real Estate and Business Financing</title>
<link rel="stylesheet" href="https://fonts.googleapis.com/css2?family=Poppins:wght@400;500;600;700;800&display=swap">
<style>
  :root {
    --page-bg: #f2f2f2;
    --brand-blue: #3f64c2;
    --brand-blue-deep: #2f52ad;
    --brand-blue-light: #5a7fd3;
    --text-blue: #3859b3;
    --panel-white: #ffffff;
    --band-dark: #2d2e34;
    --text-grey: #505050;
    --rule-grey: #5c5c5c;
    --white: #ffffff;
  }
  * { margin: 0; padding: 0; box-sizing: border-box; }
  html, body {
    width: 996px; height: 1200px; overflow: hidden;
    background: var(--page-bg);
    font-family: "Poppins", sans-serif;
  }
  .banner {
    position: absolute; left: 48px; top: 375px;
    width: 900px; height: 450px;
    background: var(--panel-white);
    box-shadow: 0 3px 8px rgba(0,0,0,0.25);
    overflow: hidden;
  }
  .headline-band {
    position: absolute; left: 0; top: 0; width: 900px; height: 184px;
    background: linear-gradient(100deg, var(--brand-blue-deep) 0%, var(--brand-blue) 55%, var(--brand-blue-light) 100%);
  }
  .portrait {
    position: absolute; left: 655px; top: 0; width: 245px; height: 339px;
    background: linear-gradient(180deg, #8a93a6 0%, #c9b2a3 35%, #ece9e6 55%, #2c2f3a 70%, #23252e 100%);
  }
  .headline {
    position: absolute; left: 28px; top: 18px;
    color: var(--white); font-weight: 800; font-size: 58px;
    line-height: 54px; letter-spacing: -0.5px; text-transform: uppercase;
    white-space: nowrap;
  }
  .subline {
    position: absolute; left: 26px; top: 134px;
    color: var(--white); font-weight: 400; font-size: 35px; line-height: 42px;
    white-space: nowrap;
  }
  .brand-mark {
    position: absolute; left: 29px; top: 204px;
    width: 110px; height: 110px; border-radius: 50%;
    border: 4px solid var(--brand-blue);
  }
  .brand-rule {
    position: absolute; left: 150px; top: 202px; width: 3px; height: 113px;
    background: var(--rule-grey);
  }
  .company-name {
    position: absolute; left: 160px; top: 236px;
    color: var(--text-blue); font-weight: 500; font-size: 17px; line-height: 22px;
    white-space: nowrap;
  }
  .company-tagline {
    position: absolute; left: 160px; top: 262px;
    color: var(--text-grey); font-weight: 400; font-size: 14.5px; line-height: 20px;
    white-space: nowrap;
  }
  .service-list {
    position: absolute; left: 472px; top: 192px; list-style: none;
  }
  .service-list li {
    display: flex; align-items: center; gap: 8px;
    height: 36px; color: var(--text-blue); font-weight: 600; font-size: 24px;
    white-space: nowrap;
  }
  .service-list svg { width: 17px; height: 17px; }
  .contact-band {
    position: absolute; left: 0; top: 339px; width: 900px; height: 111px;
  }
  .contact-heading {
    position: absolute; left: 29px; top: 350px;
    color: var(--white); font-size: 28px; line-height: 36px; font-weight: 400;
    white-space: nowrap;
  }
  .contact-heading strong { font-weight: 500; }
  .contact-row {
    position: absolute; left: 29px; top: 394px; height: 40px;
    display: flex; align-items: center;
    color: var(--white); font-size: 28px; font-weight: 500;
    white-space: nowrap;
  }
  .contact-row svg { width: 22px; height: 22px; margin-right: 7px; }
  .contact-divider {
    width: 2px; height: 38px; background: var(--white); margin: 0 11px 0 13px;
  }
  .person-name {
    position: absolute; left: 700px; top: 350px; width: 180px;
    text-align: center; color: var(--text-blue);
    font-size: 35px; line-height: 40px;
  }
  .person-name .first { display: block; font-weight: 700; }
  .person-name .last { display: block; font-weight: 400; }
</style>
</head>
<body>
  <main class="banner">
    <div class="headline-band"></div>
    <div class="portrait" role="img" aria-label="Portrait photo of the adviser in a dark suit and white shirt"></div>

    <h1 class="headline">Real Estate and<br>Business Financing</h1>
    <p class="subline">Independent Insurance Adviser</p>

    <div class="brand-mark"></div>
    <div class="brand-rule"></div>
    <p class="company-name">Weber Vermögensberatung GmbH</p>
    <p class="company-tagline">Finanzieren, Versichern, Vorsorgen</p>

    <ul class="service-list">
      <li><svg viewBox="0 0 20 20"><path d="M2 11 L7 16 L18 3" fill="none" stroke="currentColor" stroke-width="3"/></svg>Investment</li>
      <li><svg viewBox="0 0 20 20"><path d="M2 11 L7 16 L18 3" fill="none" stroke="currentColor" stroke-width="3"/></svg>Financing</li>
      <li><svg viewBox="0 0 20 20"><path d="M2 11 L7 16 L18 3" fill="none" stroke="currentColor" stroke-width="3"/></svg>Leasing</li>
      <li><svg viewBox="0 0 20 20"><path d="M2 11 L7 16 L18 3" fill="none" stroke="currentColor" stroke-width="3"/></svg>Insurance</li>
    </ul>

    <svg class="contact-band" viewBox="0 0 900 111">
      <rect x="0" y="0" width="900" height="111" fill="var(--panel-white)"/>
      <polygon points="0,0 700,0 635,111 0,111" fill="var(--band-dark)"/>
      <polygon points="635,106 900,106 900,111 632,111" fill="var(--brand-blue)"/>
    </svg>

    <p class="contact-heading">YOUR REGIONAL <strong>CONTACT AT</strong></p>
    <div class="contact-row">
      <svg viewBox="0 0 24 24"><path d="M6.5 2.5 L9.5 7 L7.5 9.5 C8.8 12.3 11.7 15.2 14.5 16.5 L17 14.5 L21.5 17.5 L19.5 21 C11 21 3 13 3 4.5 Z" fill="none" stroke="currentColor" stroke-width="2" stroke-linejoin="round"/></svg>
      <span>+43 660 214 5873</span>
      <span class="contact-divider"></span>
      <svg viewBox="0 0 24 24"><circle cx="12" cy="12" r="9.5" fill="none" stroke="currentColor" stroke-width="2"/><ellipse cx="12" cy="12" rx="4.2" ry="9.5" fill="none" stroke="currentColor" stroke-width="1.6"/><path d="M3 9 H21 M3 15 H21" stroke="currentColor" stroke-width="1.6"/></svg>
      <span>www.der-weber.at</span>
    </div>

    <p class="person-name"><span class="first">MARTIN</span><span class="last">WEBER</span></p>
  </main>
</body>
</html>
```